Tall Fern Roofing Business Card

Need a business card with the logo that was designed here

Contact Information for Business Card

Name, Title, Phone, Email, Website, Company name

```html
<!DOCTYPE html>
<html lang="en">
<head>
<meta charset="utf-8">
<title>Tall Fern Roofing Business Card</title>
<link rel="stylesheet" href="https://fonts.googleapis.com/css2?family=Montserrat:wght@500;600;700&family=Lato:wght@400&display=swap">
<style>
  :root {
    --stage: #262728;
    --brand-blue: #1f77c2;
    --blue-light: #2a8ae0;
    --blue-deep: #1a66a8;
    --steel-grey: #9a9b9d;
    --paper: #ffffff;
  }
  html, body {
    margin: 0;
    width: 1200px;
    height: 1015px;
    overflow: hidden;
    background: var(--stage);
  }
  .stage {
    position: relative;
    width: 1200px;
    height: 1015px;
  }
  .card {
    position: absolute;
    left: 240px;
    width: 720px;
    height: 411px;
    overflow: hidden;
    box-shadow: 0 14px 34px rgba(0,0,0,0.55);
  }
  .card-back { top: 72px; background: var(--brand-blue); }
  .card-front { top: 532px; background: var(--paper); }
  .card svg.art { position: absolute; inset: 0; }
  .back-texture {
    position: absolute;
    inset: 0;
    background: linear-gradient(160deg, var(--blue-deep) 0%, var(--blue-light) 45%, var(--brand-blue) 100%);
  }
  .wordmark {
    position: absolute;
    display: flex;
    align-items: center;
    gap: 14px;
    font-family: "Montserrat", sans-serif;
    font-weight: 700;
    letter-spacing: 1px;
    white-space: nowrap;
  }
  .wordmark .mark-square { width: 22px; height: 22px; }
  .card-back .wordmark {
    left: 180px; top: 182px;
    font-size: 40px; color: var(--paper);
  }
  .card-back .mark-square { background: var(--paper); }
  .card-front .wordmark {
    left: 150px; top: 96px;
    font-size: 40px; color: var(--brand-blue);
  }
  .card-front .mark-square { background: var(--brand-blue); }
  .holder {
    position: absolute;
    left: 60px; top: 300px;
    color: var(--paper);
  }
  .holder-name {
    font-family: "Montserrat", sans-serif;
    font-weight: 700;
    font-size: 25px;
    letter-spacing: 0.5px;
    margin: 0;
  }
  .holder-title {
    font-family: "Lato", sans-serif;
    font-size: 18px;
    margin: 4px 0 0 56px;
  }
  .divider {
    position: absolute;
    left: 372px; top: 262px;
    width: 1px; height: 112px;
    background: rgba(255,255,255,0.45);
  }
  .contact-list {
    position: absolute;
    left: 400px; top: 262px;
    margin: 0; padding: 0;
    list-style: none;
    color: var(--paper);
    font-family: "Lato", sans-serif;
    font-size: 17px;
  }
  .contact-list li {
    display: flex;
    align-items: center;
    gap: 10px;
    height: 32px;
  }
  .contact-list svg { width: 18px; height: 18px; flex: none; }
</style>
</head>
<body>
<main class="stage">

  <section class="card card-back" aria-label="Card back">
    <div class="back-texture" role="img" aria-label="Abstract blue geometric background"></div>
    <div class="wordmark"><span class="mark-square"></span>Tall Fern Roofing</div>
  </section>

  <section class="card card-front" aria-label="Card front">
    <svg class="art" viewBox="0 0 720 411" aria-hidden="true">
      <polygon points="0,262 720,116 720,411 0,411" fill="var(--steel-grey)"/>
      <polygon points="0,270 720,124 720,411 0,411" fill="var(--brand-blue)"/>
    </svg>
    <div class="wordmark"><span class="mark-square"></span>Tall Fern Roofing</div>

    <div class="holder">
      <p class="holder-name">MARCUS BELL</p>
      <p class="holder-title">Managing Director</p>
    </div>

    <div class="divider"></div>

    <ul class="contact-list">
      <li>
        <svg viewBox="0 0 24 24" aria-hidden="true"><path fill="#fff" d="M6.6 10.8a15.1 15.1 0 0 0 6.6 6.6l2.2-2.2c.3-.3.7-.4 1-.2 1.1.4 2.3.6 3.6.6.6 0 1 .4 1 1V20c0 .6-.4 1-1 1C10.6 21 3 13.4 3 4c0-.6.4-1 1-1h3.5c.6 0 1 .4 1 1 0 1.3.2 2.5.6 3.6.1.3 0 .7-.2 1z"/></svg>
        <span>044-987 654 321</span>
      </li>
      <li>
        <svg viewBox="0 0 24 24" aria-hidden="true"><rect x="2" y="5" width="20" height="14" fill="#fff"/><path d="M2 5l10 8 10-8" fill="none" stroke="var(--brand-blue)" stroke-width="1.6"/></svg>
        <span>info@tallfernroofing.com</span>
      </li>
      <li>
        <svg viewBox="0 0 24 24" aria-hidden="true"><g fill="none" stroke="#fff" stroke-width="1.8"><circle cx="12" cy="12" r="9"/><ellipse cx="12" cy="12" rx="4" ry="9"/><path d="M3 12h18M5 7h14M5 17h14"/></g></svg>
        <span>www.tallfernroofing.com</span>
      </li>
    </ul>
  </section>

</main>
</body>
</html>
```